Design 4 pages for an event discovery website

This is a contest for the design of 4 pages for an events discovery website. The feature is part of the new sign-up process.

Please see the attached document for a full scope, mockups and the parent category icons.

Target Market(s)

18-35 Australian event goers

Industry/Entity Type

Events

Number of Pages Required

4 page

```html
<!DOCTYPE html>
<html lang="en">
<head>
<meta charset="utf-8">
<title>Lumiva – Sign Up</title>
<link href="https://fonts.googleapis.com/css2?family=Open+Sans:wght@400;600;700&display=swap" rel="stylesheet">
<style>
  :root {
    --ink-white: #ffffff;
    --ink-soft: #f2f2f2;
    --placeholder: #a9a9a9;
    --field-border: #1a6fd6;
    --search-blue: #0a6fd0;
    --action-green: #2eb45b;
    --error-red: #e8434f;
    --footer-bg: rgba(38, 38, 38, 0.93);
    --rule: rgba(255, 255, 255, 0.55);
  }
  * { box-sizing: border-box; margin: 0; padding: 0; }
  html, body { width: 1200px; height: 795px; overflow: hidden; }
  body {
    position: relative;
    font-family: "Open Sans", Arial, sans-serif;
    color: var(--ink-white);
    background: #140d14;
  }
  .backdrop {
    position: absolute; inset: 0;
    background:
      radial-gradient(ellipse at 47% 28%, rgba(150, 40, 120, 0.55), transparent 40%),
      radial-gradient(ellipse at 88% 70%, rgba(120, 20, 30, 0.45), transparent 35%),
      radial-gradient(ellipse at 20% 60%, rgba(70, 40, 60, 0.6), transparent 45%),
      linear-gradient(180deg, #1a1418 0%, #2a1e26 45%, #1d1519 100%);
  }
  .site-header {
    position: absolute; left: 0; top: 0; width: 1200px; height: 94px;
    border-bottom: 1px solid var(--rule);
  }
  .brand {
    position: absolute; left: 60px; top: 28px;
    font-size: 31px; font-weight: 400; letter-spacing: 1px; line-height: 1;
  }
  .brand-tag {
    position: absolute; left: 61px; top: 65px; font-size: 14px;
  }
  .search {
    position: absolute; left: 688px; top: 28px; width: 211px; height: 39px;
    background: var(--search-blue); border-radius: 2px;
    font-size: 13px; padding: 10px 0 0 19px;
  }
  .search svg { position: absolute; right: 9px; top: 11px; }
  .btn {
    position: absolute; height: 40px; width: 107px;
    background: var(--action-green); border-radius: 2px;
    font-size: 17px; font-weight: 600; text-align: center; line-height: 40px;
    color: var(--ink-white);
  }
  .btn-signup { left: 912px; top: 28px; }
  .btn-login { left: 1033px; top: 28px; }
  .signup-title {
    position: absolute; left: 59px; top: 136px;
    font-size: 24px; font-weight: 600; letter-spacing: 0.5px;
  }
  .field {
    position: absolute; left: 60px; width: 264px; height: 39px;
    background: var(--ink-white); border: 1px solid var(--field-border);
    color: var(--placeholder); font-size: 13px; padding: 10px 0 0 10px;
  }
  .error {
    position: absolute; left: 336px; font-size: 13.5px; color: var(--error-red);
  }
  .btn-submit { left: 61px; top: 575px; }
  .benefits {
    position: absolute; left: 523px; top: 145px; list-style: none;
  }
  .benefits li {
    position: relative; padding-left: 32px; font-size: 16.5px; height: 33.2px;
  }
  .benefits li::before {
    content: ""; position: absolute; left: 0; top: 9px;
    width: 9px; height: 9px; border-radius: 50%; background: var(--ink-white);
  }
  .site-footer {
    position: absolute; left: 0; top: 704px; width: 1200px; height: 91px;
    background: var(--footer-bg);
  }
  .social {
    position: absolute; left: 537px; top: 22px; display: flex; gap: 5px;
  }
  .social span {
    width: 21px; height: 21px; background: var(--ink-soft); border-radius: 3px;
  }
  .copyright {
    position: absolute; left: 0; width: 1200px; top: 56px;
    text-align: center; font-size: 12px; font-weight: 700;
  }
</style>
</head>
<body>
  <div class="backdrop" role="img" aria-label="Photo of young people celebrating at a party under falling confetti"></div>

  <header class="site-header">
    <div class="brand">LUMIVA</div>
    <div class="brand-tag">Find Events</div>
    <div class="search">Search
      <svg width="18" height="18" viewBox="0 0 18 18"><circle cx="7.5" cy="7.5" r="5.3" fill="none" stroke="#fff" stroke-width="2.6"/><line x1="11.5" y1="11.5" x2="16" y2="16" stroke="#fff" stroke-width="3" stroke-linecap="round"/></svg>
    </div>
    <div class="btn btn-signup">SIGN UP</div>
    <div class="btn btn-login">LOGIN</div>
  </header>

  <h1 class="signup-title">SIGN UP</h1>
  <div class="field" style="top:191px">User Name</div>
  <div class="error" style="top:200px">* Error Message</div>
  <div class="field" style="top:248px">Email Address</div>
  <div class="error" style="top:255px">* Error Message</div>
  <div class="field" style="top:301px">Password</div>
  <div class="field" style="top:354px">Conform Password</div>
  <div class="field" style="top:406px">First Name</div>
  <div class="field" style="top:461px">Last Name</div>
  <div class="field" style="top:515px">Date of Birth</div>
  <div class="btn btn-submit">SIGN UP</div>

  <ul class="benefits">
    <li>Get personalised event recommendations</li>
    <li>Get notified about your favourite events - never miss out again</li>
    <li>Follow all your favourite artists, musicians, teams and players in one place</li>
    <li>Follow your favourite local venues to know everything happening there</li>
    <li>Get curated news and feature content on your favourite artists (coming soon)</li>
    <li>Invite your mates to events via Mateline (ML sign-up only)</li>
  </ul>

  <footer class="site-footer">
    <div class="social"><span></span><span></span><span></span><span></span><span></span></div>
    <div class="copyright">Copyright © 2015 lumiva. All Rights Reserved.</div>
  </footer>
</body>
</html>
```